Brenvo label design for gift tea

We want to create a luxury box for our brand of tea , its called :
" Kestrel leaf and bark"
the blend for this box is called: Kestrel Regal .
We need a label for a square gift box .( see last attachments for die cut template)
We presently have a square box for ANOTHER BRAND (called MRS Pembury's brew ) and we will use the same template for this new LUXURY box, we want you to design .
We will use the same key cut template ,SQUARE TEMPLATE FOR SQUARE BOX ie square box, 87mm square i.e 87x87x87 , mm.
(for BACK GROUND INFORMATION , we have a rectangular retail box for the " kestrel leaf and bark" brand , IT'S RECTULAR box , printed cardboard box with logo on it , ,see attachment , for pdf , its the 5th attachment.)
The new design for the Luxury box should be DIFFERENT from this ,our existing retail box , it's important that the new lux box looks expensive, VERY IMPORTANT ,
The box used by HOLWICK and TRASK for their gift tea could be a good place to go for inspiration www.hoolwickandtrask.example
also we like the pattern used and the colour on holwick and trask gift boxes .
The new label needs to make the new square box look like a LUXURARY brand. The label should have the name :
" Kestrel Leaf and Bark ", on it
Please note , You do not have to use the logo we presently have on the retail box
However , we do like the top of our present retail box where it says
"KESTREL
LEAF & BARK
see last attachment
Please note :
on the box , we need info:, storage instructions , how to make , best before date , where packed , address of company, face book, instagram, twitter ,logo etc (please see details uploaded from rear of retail box ,
Ingredients :
Earl Grey Blue Flower, bergamot flavour
Preparation Instructions:
brew 1 teaspoon (2.5g) per 200ml water. Infuse in freshly boiled water (98 degrees C) for 3-5 minutes.
Storage:
Store in a dry place, once opened best consumed within 3 months.

packed by QLV
Batch No:
Best Before Date: xx/xx/xx
www.kestrelleafandbark.example
We also need , the following on the box ,
which is the story of the brand:
"We are 3 Sisters from Persia, our dad was a merchant who travelled the Silk Road . We dreamed someday we too could go on adventures and now today are dreams are real! Our mission ? to bring everyone together, despite their differences with
PEACE, LOVE & JOY "

WE SHOULD also HAVE THE FOLLOWING STATEMENT ON THE REAR of the box:
Plant -based and Plastic -free! Our product is completely natural .
PACKAGING: Made from sustainably sourced materials and printed using vegetable water inks.
Find out more at:

Please see attachment for photograph of existing rear labels from retail box for kestrel leaf and bark

: Kestrel regal
bar code :5091234567893
check out this company for a retail persian box , not exactly what we want but it might give inspiration

https://kestrelbrew.example/collections/kestrel-brews

here is a link to some images of persian tea boxes
https://www.searchly.example/find?q=iranian+tea+boxes

Target Market(s)

PEOPLE INTERESTED IN HIGH END TEA

Industry/Entity Type

RETAIL FOOD AND DRINK

Colors
0094D4
00A9DD
6FCCEA
C7EBF8
E9F6FB

Requirements
Must have
• look expensive gift product
Nice to have
• easy to read , name of type of tea eg "Marigold brew " should be clear
Should not have
• front label should not be too crowded

```html
<!DOCTYPE html>
<html lang="en">
<head>
<meta charset="utf-8">
<title>Kestrel Regal – Gift Box Panels</title>
<link href="https://fonts.googleapis.com/css2?family=Cinzel:wght@400;600;700&family=Cormorant+Garamond:wght@500;600&display=swap" rel="stylesheet">
<style>
  :root{
    --teal:#5db9a8;
    --teal-deep:#2f9d86;
    --teal-soft:#8fd2c4;
    --band:#c2e6e4;
    --navy:#18284a;
    --gold:#c9a14a;
    --gold-light:#e6c775;
    --paper:#ffffff;
    --ink:#1a1a1a;
    --backdrop:#f2f4f4;
  }
  *{box-sizing:border-box;margin:0;padding:0}
  html,body{width:1200px;height:1200px;overflow:hidden;background:var(--backdrop)}
  body{position:relative;font-family:"Cormorant Garamond",Georgia,serif;color:var(--ink)}

  .panel{position:absolute;width:500px;height:500px;overflow:hidden;box-shadow:0 2px 10px rgba(0,0,0,.12)}
  .panel-pattern{position:absolute;inset:0;background:radial-gradient(circle at 50% 50%,var(--teal-soft) 0%,var(--teal) 75%)}

  /* top lid */
  .panel--top{left:610px;top:60px}
  .lid-medallion{position:absolute;left:110px;top:110px;width:280px;height:280px;border-radius:50%;
    background:radial-gradient(circle at 50% 45%,#1f6b6a 0%,#152a44 75%);
    border:6px solid var(--gold);display:flex;flex-direction:column;align-items:center;justify-content:center}
  .lid-medallion .brand-name{color:var(--gold-light)}
  .lid-medallion .brand-main{font-size:44px}
  .lid-medallion .brand-sub{font-size:17px}

  /* brand wordmark (text only) */
  .brand-name{font-family:"Cinzel",Georgia,serif;font-weight:700;color:var(--navy);text-align:center;line-height:1}
  .brand-main{display:block;font-size:62px;letter-spacing:1px}
  .brand-sub{display:block;font-size:20px;letter-spacing:6px;margin-top:4px}

  .band{position:absolute;left:0;right:0;background:var(--band)}
  .band-edge{position:absolute;left:0;right:0;height:12px;background:var(--teal-soft)}

  /* front */
  .panel--front{left:610px;top:580px}
  .panel--front .band{top:40px;height:150px}
  .panel--front .band-edge.upper{top:28px}
  .panel--front .band-edge.lower{top:190px}
  .panel--front .brand-name{position:absolute;top:58px;left:0;right:0}
  .arch{position:absolute;left:70px;top:195px;width:360px;height:290px;background:linear-gradient(180deg,#7fcbbb,#4fae9a);border-radius:180px 180px 0 0/60px 60px 0 0}
  .emblem-dot{position:absolute;left:234px;top:178px;width:32px;height:42px;border-radius:50%;background:var(--navy);border:3px solid var(--gold)}
  .label-card{position:absolute;left:115px;top:232px;width:270px;height:200px;background:var(--paper);
    border:4px solid var(--gold);outline:2px solid var(--gold-light);outline-offset:-9px;
    display:flex;flex-direction:column;align-items:center;justify-content:center;text-align:center}
  .blend-name{font-family:"Cinzel",Georgia,serif;font-weight:600;font-size:40px;line-height:1;color:var(--ink)}
  .blend-variant{display:flex;align-items:center;gap:8px;font-family:"Cinzel",Georgia,serif;font-weight:600;font-size:24px;margin-top:4px}
  .blend-variant::before,.blend-variant::after{content:"";width:40px;height:2px;background:var(--gold)}
  .blend-desc{font-family:"Cinzel",Georgia,serif;font-size:13px;line-height:1.15;margin-top:10px;letter-spacing:.3px}
  .net-weight{font-family:"Cinzel",Georgia,serif;font-weight:700;font-size:11px;margin-top:10px}
  .footer-band{position:absolute;left:40px;right:40px;bottom:30px;height:60px;background:linear-gradient(90deg,#3fa890,#6cc3b0,#3fa890);display:flex;align-items:center;justify-content:center}
  .site-pill{background:#a8ddd5;border-radius:20px;padding:6px 26px;font-family:"Cinzel",Georgia,serif;font-weight:700;font-size:11px;color:var(--teal-deep);letter-spacing:.5px}

  /* side */
  .panel--side{left:90px;top:580px}
  .panel--side .band{top:40px;height:150px}
  .panel--side .band-edge.upper{top:28px}
  .panel--side .band-edge.lower{top:190px}
  .panel--side .brand-name{position:absolute;top:58px;left:0;right:0}
  .info-arch{position:absolute;left:60px;top:215px;width:380px;height:180px;background:rgba(255,255,255,.12);border-radius:190px 190px 0 0/40px 40px 0 0;
    padding:18px 30px 0;text-align:center;color:#1e3a3a}
  .info-title{font-family:"Cinzel",Georgia,serif;font-size:13px;color:var(--gold);font-weight:600;letter-spacing:.5px}
  .info-text{font-size:15px;line-height:1.2;margin:3px 0 8px}
  .eco-box{position:absolute;left:40px;right:40px;bottom:28px;height:72px;background:linear-gradient(90deg,#3fa890,#6cc3b0,#3fa890);
    padding:10px 18px;font-size:12px;line-height:1.2;color:#103b33;text-align:center}
</style>
</head>
<body>

<section class="panel panel--top" aria-label="Box lid">
  <div class="panel-pattern" role="img" aria-label="Repeating geometric star lattice pattern in teal"></div>
  <div class="lid-medallion" role="img" aria-label="Dark teal medallion with gold ornamental frame">
    <div class="brand-name"><span class="brand-main">KESTREL</span><span class="brand-sub">LEAF &amp; BARK</span></div>
  </div>
</section>

<section class="panel panel--side" aria-label="Side panel with instructions">
  <div class="panel-pattern" role="img" aria-label="Repeating geometric star lattice pattern in teal"></div>
  <div class="band-edge upper"></div>
  <div class="band"></div>
  <div class="band-edge lower"></div>
  <div class="brand-name"><span class="brand-main">KESTREL</span><span class="brand-sub">LEAF &amp; BARK</span></div>
  <div class="info-arch">
    <p class="info-title">PREPARATION</p>
    <p class="info-text">Brew 1 teaspoon (2.5g) per 200ml water. Infuse in freshly boiled water (98 degrees C) for 3-5 minutes.</p>
    <p class="info-title">STORAGE</p>
    <p class="info-text">Store in a dry place, once opened best consumed within 3 months.</p>
  </div>
  <div class="eco-box">Plant-based and Plastic-free! Our product is completely natural. PACKAGING: Made from sustainably sourced materials and printed using vegetable water inks. Find out more at: www.kestrelleafandbark.example</div>
</section>

<section class="panel panel--front" aria-label="Front panel">
  <div class="panel-pattern" role="img" aria-label="Repeating geometric star lattice pattern in teal"></div>
  <div class="band-edge upper"></div>
  <div class="band"></div>
  <div class="band-edge lower"></div>
  <div class="brand-name"><span class="brand-main">KESTREL</span><span class="brand-sub">LEAF &amp; BARK</span></div>
  <div class="arch" role="img" aria-label="Arched panel with fine arabesque floral ornament"></div>
  <div class="emblem-dot"></div>
  <div class="label-card">
    <h1 class="blend-name">KESTREL</h1>
    <p class="blend-variant">REGAL</p>
    <p class="blend-desc">EARL GREY BLUE FLOWER,<br>BERGAMOT FLAVOUR</p>
    <p class="net-weight">NET WT 125G | 4.4 OZ</p>
  </div>
  <div class="footer-band" role="img" aria-label="Ornamental floral scroll band">
    <span class="site-pill">WWW.KESTRELLEAFANDBARK.EXAMPLE</span>
  </div>
</section>

</body>
</html>
```